Business Card for Industrial Distributor

We need a business card design for an industrial distributor. We sell machine parts for the manufacturing and oil industry. We would like the cards to look clean and modern but with a touch of industry.

Our colors are blue/white.

Please feel free to visit our website www.korvelpartsco.com

Target Market(s)

mexican manufacturers in the automobile/aerospace industry

Industry/Entity Type

Industrial

Colors
ffffff
0555a3

```html
<!DOCTYPE html>
<html lang="en">
<head>
<meta charset="utf-8">
<title>Korvel Business Card</title>
<link rel="stylesheet" href="https://fonts.googleapis.com/css2?family=Source+Sans+3:wght@400;600;700&display=swap">
<style>
  :root {
    --backdrop: #e8e8e8;
    --card: #ffffff;
    --brand-navy: #27348f;
    --brand-blue: #2055a0;
    --name-blue: #1f5aa6;
    --ink: #111111;
  }
  html, body {
    margin: 0;
    padding: 0;
    width: 1200px;
    height: 900px;
    overflow: hidden;
    background: var(--backdrop);
    font-family: "Source Sans 3", "Myriad Pro", sans-serif;
  }
  .canvas {
    position: relative;
    width: 1200px;
    height: 900px;
    background: radial-gradient(ellipse at 50% 30%, #ececec 0%, var(--backdrop) 70%);
  }
  .card {
    position: absolute;
    left: 334px;
    width: 561px;
    height: 346px;
    background: var(--card);
    overflow: hidden;
    box-shadow: 0 1px 2px rgba(0,0,0,0.08);
  }
  .card--front { top: 42px; }
  .card--back { top: 461px; }

  .front-arc {
    position: absolute;
    left: 0;
    top: 0;
  }
  .wordmark {
    position: absolute;
    font-weight: 700;
    color: var(--brand-navy);
    letter-spacing: 0.5px;
    line-height: 1;
    white-space: nowrap;
  }
  .card--front .wordmark {
    left: 280px;
    top: 17px;
    transform: translateX(-50%);
    font-size: 58px;
  }
  .identity {
    position: absolute;
    left: 280px;
    transform: translateX(-50%);
    text-align: center;
    white-space: nowrap;
  }
  .identity--person { top: 106px; }
  .person-name {
    margin: 0;
    font-size: 28px;
    font-weight: 600;
    color: var(--name-blue);
    line-height: 32px;
  }
  .person-role {
    margin: 0;
    font-size: 22px;
    font-weight: 400;
    color: var(--ink);
    line-height: 24px;
  }
  .contact-list {
    top: 191px;
    margin: 0;
    padding: 0;
    list-style: none;
    font-size: 17px;
    color: var(--ink);
    line-height: 21.5px;
  }
  .contact-list b { font-weight: 600; }
  .address {
    position: absolute;
    left: 280px;
    top: 308px;
    transform: translateX(-50%);
    margin: 0;
    font-size: 17px;
    color: var(--ink);
    white-space: nowrap;
  }

  .brand-lockup {
    position: absolute;
    left: 60px;
    top: 130px;
    display: flex;
    align-items: center;
    gap: 14px;
  }
  .brand-dot {
    width: 86px;
    height: 86px;
    border-radius: 50%;
    background: var(--brand-blue);
  }
  .card--back .wordmark {
    position: static;
    font-size: 84px;
  }
</style>
</head>
<body>
  <main class="canvas">
    <section class="card card--front" aria-label="Card front">
      <svg class="front-arc" width="120" height="346" viewBox="0 0 120 346" aria-hidden="true">
        <circle cx="-131" cy="173" r="217" fill="var(--brand-blue)"/>
      </svg>
      <div class="wordmark">Korvel</div>
      <div class="identity identity--person">
        <p class="person-name">Daniel Hargrove</p>
        <p class="person-role">Founder</p>
      </div>
      <ul class="identity contact-list">
        <li><b>P:</b> 312-555-0148</li>
        <li><b>M:</b> 312-555-0148</li>
        <li><b>E:</b> info@korvelpartsco.com</li>
        <li>www.korvelpartsco.com</li>
      </ul>
      <p class="address">240 W. Harmon Suite 810, Chicago, Illinois 60607</p>
    </section>

    <section class="card card--back" aria-label="Card back">
      <div class="brand-lockup">
        <span class="brand-dot" aria-hidden="true"></span>
        <span class="wordmark">Korvel</span>
      </div>
    </section>
  </main>
</body>
</html>
```